Design a New Business Card for Our Company

We are looking for fresh, unique, and a modern business card that reflects our roots as digital marketing agency focused on SEM.

Industry/Entity Type

Marketing

Contact Information for Business Card

looking for very unique out of the box designs. clean and modern that compliments our logo

Requirements
Must have
• colors should match our logo
• Front should have name, address, email, and phone/fax of the person, phone/fax are the same number
• back should have our url

```html
<!DOCTYPE html>
<html lang="en">
<head>
<meta charset="utf-8">
<title>Larkspire Solutions – Business Card</title>
<link rel="stylesheet" href="https://fonts.googleapis.com/css2?family=Source+Sans+3:wght@400;600&display=swap">
<style>
  :root {
    --backdrop: #141414;
    --card-white: #ffffff;
    --brand-blue: #5e98d2;
    --stripe-light: #6aa6dc;
    --stripe-dark: #5c94cf;
    --name-grey: #a9a9a9;
    --ink: #333333;
    --on-blue: #ffffff;
  }
  * { margin: 0; padding: 0; box-sizing: border-box; }
  html, body { width: 1200px; height: 900px; overflow: hidden; }
  body {
    background: var(--backdrop);
    font-family: "Source Sans 3", "Myriad Pro", Arial, sans-serif;
    position: relative;
  }
  .card {
    position: absolute;
    top: 170px;
    width: 347px;
    height: 561px;
    overflow: hidden;
  }
  .card--front { left: 259px; background: var(--card-white); }
  .card--back {
    left: 631px;
    background: repeating-linear-gradient(90deg,
      var(--stripe-light) 0 24px,
      var(--stripe-dark) 24px 50px);
  }
  .card__bands { position: absolute; inset: 0; }
  .company {
    position: absolute;
    left: 0; width: 100%;
    top: 76px;
    text-align: center;
  }
  .company__dot {
    display: block;
    width: 84px; height: 84px;
    margin: 0 auto 16px;
    border-radius: 50%;
    background: var(--brand-blue);
  }
  .company__name {
    font-size: 26px;
    font-weight: 600;
    color: var(--name-grey);
  }
  .person {
    position: absolute;
    left: 0; width: 100%;
    top: 299px;
    text-align: center;
    color: var(--ink);
  }
  .person__name {
    font-size: 22px;
    font-weight: 600;
    color: var(--brand-blue);
    letter-spacing: 0.3px;
    line-height: 28px;
  }
  .person__title { font-size: 15px; line-height: 24px; }
  .contact {
    list-style: none;
    margin-top: 23px;
    font-size: 15px;
    line-height: 22px;
  }
  .contact__item { display: flex; justify-content: center; align-items: center; gap: 8px; }
  .contact__icon { width: 11px; height: 11px; fill: var(--brand-blue); }
  .address {
    font-style: normal;
    margin-top: 28px;
    font-size: 15px;
    line-height: 17px;
  }
  .back-name, .back-url {
    position: absolute;
    white-space: nowrap;
    color: var(--on-blue);
    font-weight: 600;
    transform: translate(-50%, -50%) rotate(-90deg);
  }
  .back-name {
    left: 185px; top: 230px;
    font-size: 38px;
  }
  .back-url {
    left: 286px; top: 272px;
    font-size: 15px;
  }
  .back-dot {
    position: absolute;
    left: 157px; top: 425px;
    width: 56px; height: 56px;
    border-radius: 50%;
    background: var(--on-blue);
  }
</style>
</head>
<body>

<section class="card card--front" aria-label="Business card front">
  <svg class="card__bands" width="347" height="561" viewBox="0 0 347 561" aria-hidden="true">
    <path d="M86 0 H255 V42 Q170.5 20 86 42 Z" fill="var(--brand-blue)"/>
    <path d="M86 561 H255 V513 Q170.5 530 86 513 Z" fill="var(--brand-blue)"/>
  </svg>

  <div class="company">
    <span class="company__dot" aria-hidden="true"></span>
    <p class="company__name">Larkspire</p>
  </div>

  <div class="person">
    <h1 class="person__name">ETHAN COLE</h1>
    <p class="person__title">Managing Director</p>
    <ul class="contact">
      <li class="contact__item">
        <svg class="contact__icon" viewBox="0 0 12 12" aria-hidden="true"><path d="M1 4 Q6 0 11 4 L9 5.5 L8 4 H4 L3 5.5 Z M2.5 6.5 H9.5 V11 H2.5 Z"/></svg>
        <span>555-204-7316</span>
      </li>
      <li class="contact__item">
        <svg class="contact__icon" viewBox="0 0 12 12" aria-hidden="true"><path d="M1 2.5 H11 V9.5 H1 Z M1.6 3 L6 6.4 L10.4 3" fill="var(--brand-blue)" stroke="#fff" stroke-width="0.9"/></svg>
        <span>hello@larkspire.com</span>
      </li>
    </ul>
    <address class="address">
      48 Harbor Lane, Suite 210<br>
      Westbrook, 204815
    </address>
  </div>
</section>

<section class="card card--back" aria-label="Business card back">
  <p class="back-name">Larkspire Solutions</p>
  <p class="back-url">www.larkspire.com</p>
  <span class="back-dot" aria-hidden="true"></span>
</section>

</body>
</html>
```